Velvet Moon Wheel Method Needs a Website

I require a Wordpress website so that I can do simple edits myself. I want it to be a fairly simple design as the videos and the text will speak for themselves.
The concept is simple, we have developed a revolutionary roulette system that proves the game is NOT random. This breakthrough is absolutely massive. We are offering a 12-part training course to take a beginner to a professional at their own pace through watching videos made by our roulette genius.
Roulette and casinos have a glitzy feel about them and this should be reflected in the style of the site. The roulette wheel, table and chips are very evocative and pictures of these would be good.
There is a home page and 5 other pages containing sub-pages. These should be interlinked and it must be easy to get back to the home page from anywhere on the site.
Coinvey links should appear at the bottom of each page.
I really need the site in a hurry as we were let down badly by the last developer we hired who went on holiday and left us in the lurch.

Target Market(s)

Gamblers, betting community, opportunity seekers

Coding

Coded - Design and coding required

Number of Pages Required

1 page

Font styles to use
Sans Serif

Requirements
Must have
• At least two videos on the Home page.
• Coinvey details on every page and tab.
• A box for name and email address for interested parties to leave their details.

```html
<!DOCTYPE html>
<html lang="en">
<head>
<meta charset="utf-8">
<title>Velvet Moon Wheel Method</title>
<link href="https://fonts.googleapis.com/css2?family=Roboto:wght@400;500;700&family=Open+Sans:ital,wght@0,400;0,600;1,400&display=swap" rel="stylesheet">
<style>
:root{
  --red:#e0262b;
  --red-dark:#c71e23;
  --navy:#1f2b3d;
  --navy-2:#27344a;
  --topbar:#1c2636;
  --ink:#222;
  --body:#666;
  --light:#f7f7f7;
  --line:#e2e2e2;
  --footer:#0b0b0b;
  --footer-text:#bdbdbd;
  --star:#f2b01e;
}
*{margin:0;padding:0;box-sizing:border-box}
html,body{width:1200px;height:2731px;overflow:hidden}
body{font-family:"Open Sans",Arial,sans-serif;color:var(--body);background:#fff;position:relative}
.section{position:absolute;left:0;width:1200px}
.abs{position:absolute}
h1,h2,h3,h4{font-family:"Roboto",Arial,sans-serif;font-weight:500;color:var(--ink)}

/* top bar */
.topbar{top:0;height:33px;background:var(--topbar);font-size:11px;color:#a9b2c0}
.topbar .item{position:absolute;top:9px;display:flex;align-items:center;gap:7px}
.topbar svg{width:11px;height:11px;fill:#a9b2c0}

/* header */
.header{top:33px;height:85px;background:#fff}
.logo{left:98px;top:22px;font-family:"Roboto",Arial,sans-serif;font-size:31px;font-weight:400;color:var(--red)}
.nav{left:509px;top:36px;display:flex;font-family:"Roboto",Arial,sans-serif;font-size:12px;font-weight:500;color:#333}
.nav span{margin-right:47px}
.nav .active{color:var(--red)}
.cart{left:1065px;top:25px;width:34px;height:34px;border-radius:50%;background:#eee;display:flex;align-items:center;justify-content:center}
.cart svg{width:14px;height:14px}
.cart .badge{position:absolute;top:-8px;right:-2px;width:18px;height:18px;border-radius:50%;background:var(--red);color:#fff;font-size:10px;text-align:center;line-height:18px}

/* hero */
.hero{top:118px;height:479px;background:radial-gradient(ellipse at 50% 95%,#7b3b1a 0%,#4a2414 30%,#231713 60%,#161314 100%)}
.hero-arrow{top:339px;width:30px;height:30px;border:2px solid #cfcfcf;border-radius:50%;display:flex;align-items:center;justify-content:center;opacity:.8}
.hero-arrow svg{width:12px;height:12px;stroke:#ddd;fill:none;stroke-width:2.4}
.hero-title{left:359px;top:184px;width:486px;height:66px;background:var(--red);color:#fff;font-family:"Roboto",Arial,sans-serif;font-weight:700;font-size:32px;text-align:center;line-height:66px}
.hero-sub{left:270px;top:259px;width:661px;height:66px;background:rgba(20,16,14,.72);color:#fff;font-size:14px;font-style:italic;font-weight:600;text-align:center;padding-top:10px;line-height:23px}

/* welcome */
.welcome{top:597px;height:392px;background:var(--light)}
.welcome h2{left:98px;top:48px;width:490px;font-size:27px;text-transform:uppercase;white-space:nowrap}
.welcome .copy{left:98px;top:92px;width:470px;font-size:11.5px;line-height:21px}
.welcome .copy p+p{margin-top:14px}
.btn{background:var(--red);color:#fff;font-family:"Roboto",Arial,sans-serif;font-size:12px;font-weight:500;text-transform:uppercase;text-align:center;border-radius:3px}
.welcome .btn{left:98px;top:297px;width:144px;height:40px;line-height:40px}
.video{left:617px;top:55px;width:485px;height:284px;background:linear-gradient(135deg,#2b3d33 0%,#3f5446 40%,#5a3528 75%,#1e1a18 100%)}
.video .play{left:206px;top:106px;width:72px;height:72px;border-radius:50%;border:3px solid rgba(255,255,255,.8);background:rgba(0,0,0,.25)}
.video .play svg{position:absolute;left:24px;top:19px;width:28px;height:30px;fill:rgba(255,255,255,.85)}

/* newsletter */
.newsletter{top:989px;height:102px;background:var(--navy)}
.newsletter .envelope{left:98px;top:20px;width:62px;height:60px}
.newsletter h3{left:177px;top:38px;font-size:21px;color:#fff;text-transform:uppercase}
.field{top:33px;height:35px;background:#fff;border-radius:2px;font-size:11px;color:#555;padding:10px 12px}
.field svg{position:absolute;right:10px;top:12px;width:11px;height:11px;fill:#777}
.newsletter .btn{left:996px;top:33px;width:104px;height:35px;line-height:35px}

/* training */
.training{top:1091px;height:404px;background:#fff}
.training h2{left:0;width:1200px;top:40px;text-align:center;font-size:27px}
.training .lead{left:200px;top:76px;width:800px;text-align:center;font-size:11.5px;line-height:22px}
.card{top:189px;width:237px;height:162px;background:#fff;border:1px solid var(--line);box-shadow:0 2px 3px rgba(0,0,0,.08);text-align:center}
.card .icon{position:absolute;left:78px;top:-46px;width:80px;height:80px;border-radius:50%;background:var(--navy);border:4px solid #fff;box-shadow:0 0 0 1px var(--line);display:flex;align-items:center;justify-content:center}
.card .icon svg{width:30px;height:30px;fill:none;stroke:#fff;stroke-width:2}
.card h4{margin-top:53px;font-size:12px;text-transform:uppercase;color:#333}
.card p{margin:8px 22px 0;font-size:11.5px;line-height:22px}
.card .more{display:block;margin-top:6px;font-size:11px;font-style:italic;color:var(--red);text-decoration:underline}

/* casinos */
.casinos{top:1495px;height:446px;background:var(--navy-2)}
.casinos h2{left:98px;top:52px;font-size:27px;color:#fff;text-transform:uppercase}
.accordion{left:98px;top:115px;width:208px;height:269px;border:1px solid #8a95a6}
.acc-head{position:absolute;left:0;width:206px;font-family:"Roboto",Arial,sans-serif;font-size:13px;font-weight:500;color:#fff;text-transform:uppercase;padding-left:22px}
.acc-head.ruled{border-top:1px solid #8a95a6}
.acc-head svg{position:absolute;right:12px;width:13px;height:13px}
.acc-item{position:absolute;left:0;width:206px;font-size:13px;color:#e6e9ee;padding-left:36px}
.acc-item.active{background:var(--red);width:214px;color:#fff}
.casino-text{left:361px;top:115px;width:430px}
.casino-text h4{font-size:14px;color:#fff;text-transform:uppercase;font-weight:700}
.casino-text p{margin-top:14px;font-size:11.5px;line-height:22px;color:#d0d5de}
.casino-text .read{display:block;margin-top:12px;font-size:11px;color:#fff;text-decoration:underline;font-family:"Roboto",Arial,sans-serif;font-weight:500}
.casino-photo{left:830px;top:87px;width:270px;height:270px;border-radius:50%;border:5px solid #fff;background:radial-gradient(circle at 40% 55%,#c7453a 0%,#8c1d1b 45%,#3b1211 100%)}

/* coaching */
.coaching{top:1941px;height:459px;background:#fff}
.coaching h3{top:54px;font-size:19px;text-transform:uppercase}
.coach-photo{left:98px;width:175px;height:138px}
.coach-body{left:293px;width:370px}
.coach-body h4{font-size:13px;color:var(--red);text-transform:uppercase;font-weight:400}
.coach-body p{margin-top:6px;font-size:11.5px;line-height:21.5px}
.stars{margin-top:3px;display:flex;gap:2px}
.stars svg{width:12px;height:12px}
.trip-panel{left:701px;top:99px;width:401px;height:309px;background:linear-gradient(180deg,#1f2634 0%,#2a2b33 55%,#4a3422 100%)}
.trip-frame{left:24px;top:25px;width:353px;height:259px;border:1px solid rgba(255,255,255,.55)}
.trip-frame h4{position:absolute;left:23px;top:38px;font-size:14px;color:#fff;text-transform:uppercase;font-weight:400}
.trip-frame p{position:absolute;left:23px;top:62px;width:320px;font-size:11px;line-height:21px;color:#fff;font-style:italic}
.trip-frame .btn{position:absolute;left:23px;top:172px;width:146px;height:44px;line-height:44px}

/* footer */
.footer{top:2400px;height:331px;background:var(--footer);color:var(--footer-text)}
.footer h5{position:absolute;top:46px;font-family:"Roboto",Arial,sans-serif;font-weight:500;font-size:15px;color:#fff;text-transform:uppercase}
.pay-name{left:98px;top:88px;font-family:"Open Sans",Arial,sans-serif;font-weight:600;font-size:30px;color:#fff;display:flex;align-items:center;gap:10px}
.pay-name i{display:block;width:26px;height:26px;background:#2d6fd1}
.pay-text{left:98px;top:156px;width:220px;font-size:11px;line-height:21px}
.links{top:84px;font-size:10.5px;text-transform:uppercase;line-height:25.5px}
.links li{list-style:none;padding-left:18px;position:relative}
.links li::before{content:"";position:absolute;left:2px;top:10px;border-left:4px solid #aaa;border-top:3px solid transparent;border-bottom:3px solid transparent}
.contact{left:725px;top:84px;font-size:11px;line-height:21px;width:250px}
.contact div{position:relative;padding-left:19px;margin-bottom:4px}
.contact svg{position:absolute;left:0;top:5px;width:11px;height:11px;fill:#bbb}
.social{left:1005px;top:84px;font-size:10.5px;text-transform:uppercase}
.social div{display:flex;align-items:center;gap:10px;height:34px}
.social i{display:block;width:25px;height:25px;border:1.5px solid #ddd;border-radius:50%}
.footer .rule{left:98px;top:268px;width:1004px;height:1px;background:#2a2a2a}
.copyright{left:0;width:1200px;top:292px;text-align:center;font-size:10.5px;color:#ccc}
</style>
</head>
<body>

<div class="section topbar">
  <div class="item" style="left:98px">
    <svg viewBox="0 0 24 24"><path d="M6.6 10.8a15.1 15.1 0 0 0 6.6 6.6l2.2-2.2c.3-.3.7-.4 1-.2 1.1.4 2.3.6 3.6.6.6 0 1 .4 1 1V20c0 .6-.4 1-1 1A17 17 0 0 1 3 4c0-.6.4-1 1-1h3.5c.6 0 1 .4 1 1 0 1.3.2 2.5.6 3.6.1.3 0 .7-.2 1z"/></svg>
    <span>Text: 07900 418 562</span>
  </div>
  <div class="item" style="left:256px">
    <svg viewBox="0 0 24 24"><path d="M2 5h20v14H2zm2 2v.5l8 5 8-5V7zm0 2.8V17h16V9.8l-8 5z"/></svg>
    <span>Email: support@velvetmoonmethod.com</span>
  </div>
  <div class="item" style="left:925px">
    <svg viewBox="0 0 24 24"><path d="M12 2a10 10 0 1 0 0 20 10 10 0 0 0 0-20zm0 2a8 8 0 1 1 0 16 8 8 0 0 1 0-16zm-1 3v6l5 3 1-1.6-4-2.4V7z"/></svg>
    <span>Monday – Friday 10 AM – 8 PM</span>
  </div>
</div>

<header class="section header">
  <div class="abs logo">Velvet Moon Method</div>
  <nav class="abs nav">
    <span class="active">HOME</span>
    <span>VELVET MOON TRAINING</span>
    <span>CASINOS</span>
    <span>COACHING</span>
    <span>LAS VEGAS</span>
  </nav>
  <div class="abs cart">
    <svg viewBox="0 0 24 24"><path d="M3 4h3l2.4 10h9.6l2-7H8M9 20a1.5 1.5 0 1 0 0-.1zm8 0a1.5 1.5 0 1 0 0-.1z" stroke="#555" stroke-width="2" fill="none"/></svg>
    <span class="badge">0</span>
  </div>
</header>

<section class="section hero" role="img" aria-label="Players around a roulette table with the spinning wheel in the foreground">
  <div class="abs hero-arrow" style="left:67px"><svg viewBox="0 0 12 12"><path d="M8 1 3 6l5 5"/></svg></div>
  <div class="abs hero-arrow" style="left:1101px"><svg viewBox="0 0 12 12"><path d="M4 1l5 5-5 5"/></svg></div>
  <div class="abs hero-title">VELVET MOON AT ROULETTE</div>
  <div class="abs hero-sub">Sed ut perspiciatis unde omnis iste natus error sit voluptatem accusantium doloremque<br>laudantium, totam rem aperiam, eaque ipsa quae ab illo inventore</div>
</section>

<section class="section welcome">
  <h2 class="abs">Welcome to Velvet Moon Method</h2>
  <div class="abs copy">
    <p>We are offering a unique opportunity to learn the Velvet Moon Wheel Method through a series of videos made by our very own roulette genius. You will learn every aspect of this amazing system at your own pace, only moving on to the next stage when you have totally mastered the previous step. We encourage our students to practise their skills in play mode and when they are completely confident and winning every</p>
    <p>Session, play with real money. This allows them to build their bankroll and pay for each video as they go along.Our course has been designed to make each step easy to learn and understand.Each video leads into the next and builds a new layer...</p>
  </div>
  <div class="abs btn">Watch This Video</div>
  <div class="abs video" role="img" aria-label="Video still of a hand placing chips beside a roulette wheel">
    <div class="abs play"><svg viewBox="0 0 28 30"><path d="M2 1l25 14L2 29z"/></svg></div>
  </div>
</section>

<section class="section newsletter">
  <svg class="abs envelope" viewBox="0 0 62 60"><path d="M4 28 31 6l27 22v28H4z" fill="#3a4659"/><path d="M4 28l27 18 27-18" fill="none" stroke="#1f2b3d" stroke-width="2"/></svg>
  <h3 class="abs">Sign up ur newsletter</h3>
  <div class="abs field" style="left:448px;width:264px">Name<svg viewBox="0 0 24 24"><path d="M12 12a5 5 0 1 0 0-10 5 5 0 0 0 0 10zm0 2c-5 0-9 2.5-9 6v2h18v-2c0-3.5-4-6-9-6z"/></svg></div>
  <div class="abs field" style="left:723px;width:262px">E-mail<svg viewBox="0 0 24 24"><path d="M2 5h20v14H2zm2 2v.5l8 5 8-5V7zm0 2.8V17h16V9.8l-8 5z"/></svg></div>
  <div class="abs btn">Sign Up</div>
</section>

<section class="section training">
  <h2 class="abs">TRAINING</h2>
  <p class="abs lead">Sed ut perspiciatis unde omnis iste natus error sit voluptatem accusantium doloremque laudantium, totam rem aperiam, eaque ipsa quae ab illo inventore veritatis et quasi architecto beatae vitae dicta sunt explicabo Nemo enim ipsam voluptatem quia voluptas</p>

  <div class="abs card" style="left:98px">
    <div class="icon"><svg viewBox="0 0 24 24"><path d="M5 4h11l3 3v13H8L5 17z M8 17V7h11"/></svg></div>
    <h4>Course Description</h4>
    <p>Sed ut perspiciatis unde omnis iste natus error sit voluptatem...</p>
    <span class="more">Click View More Information!</span>
  </div>
  <div class="abs card" style="left:353px">
    <div class="icon"><svg viewBox="0 0 24 24"><path d="M4 6h16v14H4zM4 10h16M8 3v5M16 3v5M8 13h2M12 13h2M16 13h1M8 16h2M12 16h2"/></svg></div>
    <h4>Monthly Membership</h4>
    <p>Sed ut perspiciatis unde omnis iste natus error sit voluptatem...</p>
    <span class="more">Click View More Information!</span>
  </div>
  <div class="abs card" style="left:608px">
    <div class="icon"><svg viewBox="0 0 24 24"><path d="M3 4h18v12H3zM9 20h6M12 16v4"/></svg></div>
    <h4>The Complete System</h4>
    <p>Sed ut perspiciatis unde omnis iste natus error sit voluptatem...</p>
    <span class="more">Click View More Information!</span>
  </div>
  <div class="abs card" style="left:865px">
    <div class="icon"><svg viewBox="0 0 24 24"><path d="M14 5H4v15h15v-9M10 14l1-4 8-8 3 3-8 8z"/></svg></div>
    <h4>Intellectual Property Rights</h4>
    <p>Sed ut perspiciatis unde omnis iste natus error sit voluptatem...</p>
    <span class="more">Click View More Information!</span>
  </div>
</section>

<section class="section casinos">
  <h2 class="abs">Casinos</h2>
  <div class="abs accordion">
    <div class="acc-head" style="top:0;height:51px;line-height:51px;border-bottom:1px solid #8a95a6">Reputable Casinos
      <svg viewBox="0 0 14 14" style="top:19px"><circle cx="7" cy="7" r="6" fill="none" stroke="#fff" stroke-width="1.4"/><path d="M4 7h6M7 4v6" stroke="#fff" stroke-width="1.4"/></svg></div>
    <div class="acc-item active" style="top:51px;height:31px;line-height:31px">a. Betharbor</div>
    <div class="acc-item" style="top:92px;height:30px;line-height:30px">b. Luxecasino</div>
    <div class="acc-item" style="top:132px;height:30px;line-height:30px">c. Etc. etc.</div>
    <div class="acc-head ruled" style="top:184px;height:40px;line-height:38px">Casino Bonuses
      <svg viewBox="0 0 14 14" style="top:13px"><circle cx="7" cy="7" r="6" fill="none" stroke="#fff" stroke-width="1.4"/><path d="M4 7h6M7 4v6" stroke="#fff" stroke-width="1.4"/></svg></div>
    <div class="acc-head ruled" style="top:224px;height:43px;line-height:41px">RNG vs Real Wheel
      <svg viewBox="0 0 14 14" style="top:14px"><circle cx="7" cy="7" r="6" fill="none" stroke="#fff" stroke-width="1.4"/><path d="M4 7h6M7 4v6" stroke="#fff" stroke-width="1.4"/></svg></div>
  </div>
  <div class="abs casino-text">
    <h4>Betharbor</h4>
    <p>Sed ut perspiciatis unde omnis iste natus error sit voluptatem accusantium doloremque laudantium, totam rem aperiam, eaque ipsa quae ab illo inventore veritatis Nemo enim ipsam voluptatem quia voluptas sit aspernatur aut voluptatem sequi et quasi architecto beatae vitae dicta sunt explicabo...</p>
    <p>Led ut perspiciatis unde omnis iste natus error sit voluptatem accusantium doloremque laudantium, totam rem aperiam, eaque ipsa quae ab illo inventore veritatis Nemo enim ipsam voluptatem quia voluptas sit aspernatur aut voluptatem sequi et quasi architecto beatae vitae dicta sunt explicabo...</p>
    <span class="read">READ MORE &gt;&gt;</span>
  </div>
  <div class="abs casino-photo" role="img" aria-label="Close-up of a hand spinning a red roulette wheel"></div>
</section>

<section class="section coaching">
  <h3 class="abs" style="left:98px">Coaching</h3>
  <div class="abs coach-photo" style="top:99px;background:linear-gradient(135deg,#1f6b34 0%,#2e8a45 45%,#8a2a1e 80%,#3b1b12 100%)" role="img" aria-label="Roulette wheel with chips on a green table"></div>
  <div class="abs coach-body" style="top:101px">
    <h4>Coaching Sessions</h4>
    <p>Tur tortor elit, ullamcorper non odio sollicitudin, fermentum tristique nuncurabitur eu est orci. In sodales, dui eget tempor consequat.The standard rooms can be a bit small, as with historic hotel. ipsumsera Court for brunch is not to be missed!</p>
    <div class="stars">
      <svg viewBox="0 0 24 24"><path fill="var(--star)" d="M12 2l3 7 7 .6-5.3 4.6 1.7 7.3L12 17.8 5.6 21.5l1.7-7.3L2 9.6 9 9z"/></svg>
      <svg viewBox="0 0 24 24"><path fill="var(--star)" d="M12 2l3 7 7 .6-5.3 4.6 1.7 7.3L12 17.8 5.6 21.5l1.7-7.3L2 9.6 9 9z"/></svg>
      <svg viewBox="0 0 24 24"><path fill="var(--star)" d="M12 2l3 7 7 .6-5.3 4.6 1.7 7.3L12 17.8 5.6 21.5l1.7-7.3L2 9.6 9 9z"/></svg>
      <svg viewBox="0 0 24 24"><path fill="var(--star)" d="M12 2l3 7 7 .6-5.3 4.6 1.7 7.3L12 17.8 5.6 21.5l1.7-7.3L2 9.6 9 9z"/></svg>
      <svg viewBox="0 0 24 24"><path fill="#999" d="M12 2l3 7 7 .6-5.3 4.6 1.7 7.3L12 17.8 5.6 21.5l1.7-7.3L2 9.6 9 9z"/></svg>
    </div>
  </div>
  <div class="abs coach-photo" style="top:270px;background:linear-gradient(135deg,#5a2a1a 0%,#a8563a 40%,#2f6b3a 75%,#1d2a1f 100%)" role="img" aria-label="Group of friends celebrating at a casino table"></div>
  <div class="abs coach-body" style="top:272px">
    <h4>Play-for- you</h4>
    <p>Tur tortor elit, ullamcorper non odio sollicitudin, fermentum tristique nuncurabitur eu est orci. In sodales, dui eget tempor consequat.The standard rooms can be a bit small, as with historic hotel. ipsumsera Court for brunch is not to be missed!</p>
    <div class="stars">
      <svg viewBox="0 0 24 24"><path fill="var(--star)" d="M12 2l3 7 7 .6-5.3 4.6 1.7 7.3L12 17.8 5.6 21.5l1.7-7.3L2 9.6 9 9z"/></svg>
      <svg viewBox="0 0 24 24"><path fill="var(--star)" d="M12 2l3 7 7 .6-5.3 4.6 1.7 7.3L12 17.8 5.6 21.5l1.7-7.3L2 9.6 9 9z"/></svg>
      <svg viewBox="0 0 24 24"><path fill="var(--star)" d="M12 2l3 7 7 .6-5.3 4.6 1.7 7.3L12 17.8 5.6 21.5l1.7-7.3L2 9.6 9 9z"/></svg>
      <svg viewBox="0 0 24 24"><path fill="var(--star)" d="M12 2l3 7 7 .6-5.3 4.6 1.7 7.3L12 17.8 5.6 21.5l1.7-7.3L2 9.6 9 9z"/></svg>
      <svg viewBox="0 0 24 24"><path fill="#999" d="M12 2l3 7 7 .6-5.3 4.6 1.7 7.3L12 17.8 5.6 21.5l1.7-7.3L2 9.6 9 9z"/></svg>
    </div>
  </div>

  <h3 class="abs" style="left:701px">Overseas Trip</h3>
  <div class="abs trip-panel" role="img" aria-label="Las Vegas skyline lit up at night">
    <div class="abs trip-frame">
      <h4>Las Vegas</h4>
      <p>Sed ut perspiciatis unde omnis iste natus error sit voluptatem accusantium doloremque laudantium, totam rem aperiam, eaque ipsa quae ab illo inventore veritatis et quasi architecto beatae vitae dicta sunt explicabo. Nemo enim...</p>
      <div class="btn">Get Start Today</div>
    </div>
  </div>
</section>

<footer class="section footer">
  <h5 style="left:98px">Coinvey Details</h5>
  <div class="abs pay-name"><i></i>Coinvey</div>
  <p class="abs pay-text">Nemo enim ipsam voluptatem quia volu ptas sit aspernatur aut odit aut fugit, sed quia consequuntur magni dolores eos qui ratione voluptatem...</p>

  <h5 style="left:371px">Navigation</h5>
  <ul class="abs links" style="left:371px">
    <li>Home</li><li>Velvet Moon Training</li><li>Casinos</li><li>Coaching</li><li>Las Vegas</li><li>Contact Us</li>
  </ul>

  <h5 style="left:552px">Information</h5>
  <ul class="abs links" style="left:552px">
    <li>Terms &amp; Codition</li><li>Privacy Policy</li><li>Disclaimer</li><li>Site Map</li><li>Coaching Services</li><li>Payment Info</li>
  </ul>

  <h5 style="left:725px">Contact Info</h5>
  <div class="abs contact">
    <div><svg viewBox="0 0 24 24"><path d="M12 2a7 7 0 0 0-7 7c0 5 7 13 7 13s7-8 7-13a7 7 0 0 0-7-7zm0 9.5a2.5 2.5 0 1 1 0-5 2.5 2.5 0 0 1 0 5z"/></svg>18 Harrow Lane, Velvet Moon Co.,<br>City-40210</div>
    <div><svg viewBox="0 0 24 24"><path d="M6.6 10.8a15.1 15.1 0 0 0 6.6 6.6l2.2-2.2c.3-.3.7-.4 1-.2 1.1.4 2.3.6 3.6.6.6 0 1 .4 1 1V20c0 .6-.4 1-1 1A17 17 0 0 1 3 4c0-.6.4-1 1-1h3.5c.6 0 1 .4 1 1 0 1.3.2 2.5.6 3.6.1.3 0 .7-.2 1z"/></svg>TEXT: 07900 418 562</div>
    <div><svg viewBox="0 0 24 24"><path d="M2 5h20v14H2zm2 2v.5l8 5 8-5V7zm0 2.8V17h16V9.8l-8 5z"/></svg>Email: support@velvetmoonmethod.com</div>
    <div><svg viewBox="0 0 24 24"><path d="M12 2a10 10 0 1 0 0 20 10 10 0 0 0 0-20zm0 2c.9 0 2.3 2 2.8 6H9.2c.5-4 1.9-6 2.8-6zM4.1 10h3.1c.1-2 .5-3.8 1.1-5A8 8 0 0 0 4.1 10zm0 4a8 8 0 0 0 4.2 5c-.6-1.2-1-3-1.1-5zm5.1 0c.5 4 1.9 6 2.8 6s2.3-2 2.8-6zm7.6 0c-.1 2-.5 3.8-1.1 5a8 8 0 0 0 4.2-5zm3.1-4a8 8 0 0 0-4.2-5c.6 1.2 1 3 1.1 5z"/></svg>www.velvetmoonmethod.com</div>
  </div>

  <h5 style="left:1005px">Follow Us</h5>
  <div class="abs social">
    <div><i></i>Friendbook</div>
    <div><i></i>Chirper</div>
    <div><i></i>Snapgram</div>
    <div><i></i>Pinboard</div>
  </div>

  <div class="abs rule"></div>
  <div class="abs copyright">© 2016 . VELVETMOONMETHOD | ALLRIGHTS RESERVED.</div>
</footer>

</body>
</html>
```